New Webpage for High Class Expert Witness Services Company

We are looking for a minimalist design for a webpage that just has our logo and an entry form offer to connect with one of our Liaisons.
The entry form should just ask for Name, Email, Contact Info and Description of Project.

Company Name is: The Marlowe Crest Advisory Services

Number of Pages Required

1 page

```html
<!DOCTYPE html>
<html lang="en">
<head>
<meta charset="utf-8">
<title>Connect With a Liaison — The Marlowe Crest Advisory Services</title>
<link rel="stylesheet" href="https://fonts.googleapis.com/css2?family=Marcellus&family=Young+Serif&family=Outfit:wght@400;500;600&display=swap">
<style>
  :root {
    --bg-dark: #0d0d0d;
    --bg-mid: #1b1b19;
    --ink-light: #ffffff;
    --brand-grey: #c9c9c9;
    --card: #fdf9ec;
    --field: #ebebeb;
    --field-text: #555555;
    --ink-dark: #0a0a0a;
  }
  * { box-sizing: border-box; margin: 0; padding: 0; }
  html, body { width: 1200px; height: 664px; overflow: hidden; background: var(--bg-dark); }
  .page { position: relative; width: 1200px; height: 664px; overflow: hidden; background: var(--bg-dark); }
  .hero-photo {
    position: absolute; inset: 0;
    background: radial-gradient(ellipse 260px 380px at 430px 360px, #242421 0%, var(--bg-mid) 40%, var(--bg-dark) 100%);
  }
  .brand {
    position: absolute; left: 61px; top: 92px;
    display: flex; align-items: center; gap: 12px;
    font-family: "Marcellus", serif; font-size: 19px; letter-spacing: 1.5px;
    color: var(--brand-grey); text-transform: uppercase; line-height: 1.2;
  }
  .brand-mark { width: 30px; height: 30px; background: var(--brand-grey); flex: none; }
  .headline {
    position: absolute; left: 61px; top: 250px;
    font-family: "Marcellus", serif; font-weight: 400; font-size: 59px; line-height: 63px;
    color: var(--ink-light); letter-spacing: -0.5px;
  }
  .contact-card {
    position: absolute; left: 636px; top: 46.5px; width: 524px; height: 571px;
    background: var(--card); border-radius: 30px;
  }
  .card-title {
    position: absolute; left: 0; right: 0; top: 80px;
    text-align: center; font-family: "Young Serif", serif; font-weight: 400;
    font-size: 74px; line-height: 1; color: var(--ink-dark); letter-spacing: -1px;
  }
  .field {
    position: absolute; left: 40.5px; width: 438.5px; height: 45px;
    background: var(--field); border-radius: 23px;
    display: flex; align-items: center; gap: 8px; padding-left: 22px;
    font-family: "Outfit", sans-serif; font-size: 11.5px; color: var(--field-text);
  }
  .field svg { width: 11px; height: 11px; fill: #2a2a2a; flex: none; }
  .field-name { top: 170.5px; }
  .field-email { top: 226px; }
  .field-phone { top: 281.5px; }
  .field-message { top: 336px; height: 118.5px; align-items: flex-start; padding-top: 15px; border-radius: 26px; }
  .submit {
    position: absolute; left: 40.5px; top: 464.5px; width: 438.5px; height: 45.5px;
    background: var(--ink-dark); border-radius: 23px;
    display: flex; align-items: center; justify-content: center;
    font-family: "Outfit", sans-serif; font-weight: 600; font-size: 13px; color: var(--ink-light);
  }
  .submit svg { position: absolute; right: 29px; top: 15px; width: 15px; height: 15px; fill: var(--ink-light); }
</style>
</head>
<body>
<main class="page">
  <div class="hero-photo" role="img" aria-label="Darkened photograph of a soldier in combat gear walking through smoke"></div>

  <div class="brand"><span class="brand-mark"></span><span>The Marlowe Crest<br>Advisory Services</span></div>

  <h1 class="headline">Connect<br>With a Liaison For<br>Your Project</h1>

  <section class="contact-card">
    <h2 class="card-title">Login</h2>
    <div class="field field-name">
      <svg viewBox="0 0 16 16"><circle cx="8" cy="4.5" r="3.5"/><path d="M1.5 16c0-4 3-6.5 6.5-6.5s6.5 2.5 6.5 6.5z"/></svg>First name
    </div>
    <div class="field field-email">
      <svg viewBox="0 0 16 16"><path d="M0 3h16v1.5L8 9 0 4.5z"/><path d="M0 6.3l8 4.5 8-4.5V13H0z"/></svg>Email
    </div>
    <div class="field field-phone">
      <svg viewBox="0 0 16 16"><path d="M3.6 0.8l2.3 2.8-1.3 2a9 9 0 0 0 5.8 5.8l2-1.3 2.8 2.3-1.6 2.6C8 15 1 8 1 2.4z"/></svg>Phone Number
    </div>
    <div class="field field-message">
      <svg viewBox="0 0 16 16"><ellipse cx="9" cy="7" rx="6.5" ry="5.5"/><path d="M2 16l1.5-5 3 2z"/></svg>Message
    </div>
    <div class="submit">Submit Now
      <svg viewBox="0 0 16 16"><path d="M16 0L0 6.5l5 2.3L13 3 6.5 10v5l2.8-3.6L13 14z"/></svg>
    </div>
  </section>
</main>
</body>
</html>
```